Tallowmere Cornerstones

Need to improve polish and professionalism of PPT presentation. Get consistent look and feel through whole slides, improved look and feel while maintaining the corporate standards/colour scheme, from the Brackwyn corporate presentation. Need everything in Arial font with colours consistent with the PPT template

```html
<!DOCTYPE html>
<html lang="en">
<head>
<meta charset="utf-8">
<title>Tallowmere Cornerstones – Slide Overview</title>
<link href="https://fonts.googleapis.com/css2?family=Orbitron:wght@700;800&family=Roboto:wght@400;500&display=swap" rel="stylesheet">
<style>
  :root{
    --board:#808080;
    --ink:#0f1e26;
    --red:#c8151f;
    --text:#2b2b2b;
    --circle:#e6f0f2;
    --green:#1f9d5a;
    --purple:#3a1f7a;
    --blue:#1d3fd8;
    --white:#ffffff;
  }
  *{box-sizing:border-box;margin:0;padding:0}
  html,body{width:1067px;height:1200px;overflow:hidden;background:var(--board)}
  body{position:relative;font-family:"Roboto",Arial,sans-serif;color:var(--text)}
  .slide{position:absolute;width:446px;height:250px;background:var(--white);overflow:hidden;box-shadow:0 6px 18px rgba(0,0,0,.35)}
  .col-l{left:76px}.col-r{left:545px}
  .row-1{top:73px}.row-2{top:341px}.row-3{top:609px}.row-4{top:876px}

  .top-band{position:absolute;left:0;top:0;width:100%;height:5px;background:var(--ink)}
  .brand-tab{position:absolute;right:0;top:0;width:150px;height:21px;background:var(--ink);clip-path:polygon(0 0,100% 0,100% 100%,15% 100%)}
  .brand{position:absolute;right:22px;top:3px;font-family:"Orbitron",sans-serif;font-weight:800;font-size:14px;letter-spacing:.5px;color:var(--white)}
  .footer{position:absolute;left:0;bottom:0;width:100%;height:10px;background:var(--ink)}
  .footer span{position:absolute;left:66px;top:2px;font-size:4.5px;color:var(--white)}
  .page{position:absolute;width:8px;height:8px;background:var(--red);transform:rotate(45deg);bottom:1px;left:334px}
  .page b{position:absolute;left:0;top:0;width:8px;height:8px;transform:rotate(-45deg);font-size:3.6px;color:#fff;text-align:center;line-height:8px;font-weight:500}

  .title{position:absolute;left:24px;font-family:"Orbitron",sans-serif;font-weight:700;font-size:16px;line-height:21px;color:var(--ink);letter-spacing:.2px}
  .ln{position:absolute;white-space:nowrap;line-height:1.2}
  .s8{font-size:8.4px}.s75{font-size:8px}.s7{font-size:7.4px}.s65{font-size:6.8px}.s6{font-size:6.1px}
  .strong{font-weight:500;color:#111}
  .dot::before{content:"";position:absolute;left:-10px;top:50%;width:4px;height:4px;margin-top:-2px;background:var(--red);transform:rotate(45deg)}
  .photo{position:absolute}

  /* Cover */
  .cover{background:linear-gradient(115deg,#2c4a55 0%,#16272f 38%,#0a1216 65%,#1a2e36 100%)}
  .cover .brand-big{position:absolute;left:221px;top:60px;font-family:"Orbitron",sans-serif;font-weight:800;font-size:19px;color:var(--white);letter-spacing:.6px}
  .cover .cover-title{position:absolute;left:221px;top:103px;font-family:"Orbitron",sans-serif;font-weight:700;font-size:15px;line-height:24.6px;color:var(--white);letter-spacing:.3px}
  .cover .page{left:426px;bottom:9px}

  /* Circles */
  .circle{position:absolute;width:124px;height:124px;border-radius:50%;top:89px;display:flex;flex-direction:column;align-items:center;justify-content:center;text-align:center;font-size:11px;line-height:16px;color:#111}
  .circle.light{background:var(--circle);border:1px solid #b9c4c7}
  .circle.hot{background:var(--red);border:1px solid #3a0a0d;color:#fff}
  .circle .big{font-weight:500;font-size:11.5px}
  .circle.hot .head{font-weight:500;font-size:15px;line-height:18px}

  .pill{position:absolute;height:23px;border-radius:12px;color:#fff;font-size:6.8px;font-weight:500;display:flex;align-items:center;justify-content:center}
  .pill.red{background:var(--red);font-size:7.5px}
  .pill.dark{background:var(--ink)}

  .tum{position:absolute;left:22px;top:153px;width:401px;height:64px;border:1px solid #111}
  .cell{position:absolute;color:#fff;font-size:5.8px;font-weight:500;display:flex;align-items:center;justify-content:center;border-right:1px solid #111;border-bottom:1px solid #111}
  .c-red{background:#a5151c}.c-green{background:var(--green)}.c-purple{background:var(--purple)}.c-blue{background:var(--blue)}
</style>
</head>
<body>

<section class="slide cover col-l row-1">
  <div class="brand-big">BRACKWYN</div>
  <div class="cover-title">TALLOWMERE<br>CORNERSTONES KPIS<br>&amp; PRODUCTION<br>FUNDAMENTALS</div>
  <div class="page"><b>01</b></div>
</section>

<section class="slide col-r row-1">
  <div class="photo" role="img" aria-label="Misty mine spoil heaps under a pale sky" style="left:0;top:90px;width:446px;height:150px;background:linear-gradient(180deg,#ffffff 0%,#eceeef 40%,#c9cccd 75%,#b7babb 100%)"></div>
  <div class="top-band"></div><div class="brand-tab"></div><div class="brand">BRACKWYN</div>
  <div class="title" style="top:25px">TUM – CALENDAR TIME</div>
  <p class="ln s75 dot" style="left:41px;top:65px">Calendar time means all the time in a period</p>
  <div class="circle light" style="left:24px"><span>Calendar</span><span>time for</span><span class="big">1 Year = 365 Days</span></div>
  <div class="circle hot" style="left:160px"><span class="head">Calendar</span><span class="head">time for</span><span style="margin-top:3px">October = 31 days</span></div>
  <div class="circle light" style="left:297px"><span>Calendar</span><span>time for</span><span class="big">1 shift = 12 hours</span></div>
  <div class="footer"><span>© 2024 Brackwyn Mining Solutions Inc.Strictly Confidential</span></div>
  <div class="page"><b>05</b></div>
</section>

<section class="slide col-l row-2">
  <div class="photo" role="img" aria-label="Orange excavator working in an open-pit mine at sunset" style="left:250px;top:5px;width:196px;height:235px;background:linear-gradient(90deg,#ffffff 0%,rgba(255,255,255,0) 45%),linear-gradient(180deg,#e8b27a 0%,#8a7668 40%,#5d6670 70%,#a8734c 100%)"></div>
  <div class="top-band"></div><div class="brand-tab"></div><div class="brand">BRACKWYN</div>
  <div class="title" style="top:23px;font-size:13px;line-height:17px">KPI &amp; PRODUCTION<br>FUNDAMENTALS</div>
  <p class="ln s8" style="left:25px;top:62px">At the end of this module, you will understand</p>
  <p class="ln s7 dot strong" style="left:48px;top:82px">Understand the key concepts of mine production KPIs</p>
  <p class="ln s6 dot" style="left:79px;top:102px">Time Usage Model</p>
  <p class="ln s6 dot" style="left:79px;top:115px">Availability, Utilization and Productivity</p>
  <p class="ln s6 dot" style="left:79px;top:128px">Elements of the haul cycle</p>
  <p class="ln s6 dot" style="left:79px;top:142px">Elements of the loading cycle</p>
  <p class="ln s6 dot" style="left:79px;top:155px">How changes in each of these elements impact mine production</p>
  <p class="ln s7 dot strong" style="left:48px;top:175px">The goal will be to create a baseline of understanding and a</p>
  <p class="ln s7 strong" style="left:48px;top:188px">common language across the entire mine-ops team</p>
  <p class="ln s7 dot strong" style="left:48px;top:201px">You may already understand these concepts</p>
  <p class="ln s7 dot strong" style="left:48px;top:214px">This is the time to ask questions and get clarification!</p>
  <div class="footer"><span>© 2024 Brackwyn Mining Solutions Inc.Strictly Confidential</span></div>
  <div class="page"><b>02</b></div>
</section>

<section class="slide col-r row-2">
  <div class="top-band"></div><div class="brand-tab"></div><div class="brand">BRACKWYN</div>
  <div class="title" style="top:25px">EQUIPMENT PRODUCTIVITY<br>HAUL TRUCKS</div>
  <p class="ln s75 dot" style="left:41px;top:94px">To increase productivity, we want to maximize</p>
  <p class="ln s75" style="left:41px;top:109px">truck payload while adhering to the 10/10/20 rule</p>
  <p class="ln s75 dot" style="left:41px;top:124px">No more than 10% of loads between 110%</p>
  <p class="ln s75" style="left:41px;top:139px">and 120% of Nominal Payload</p>
  <p class="ln s75 dot" style="left:41px;top:154px">No loads greater than 120% of</p>
  <p class="ln s75" style="left:41px;top:169px">Nominal Payload</p>
  <svg style="position:absolute;left:226px;top:97px" width="206" height="110" viewBox="0 0 206 110" font-family="Roboto, Arial, sans-serif">
    <text x="6" y="44" font-size="4" transform="rotate(-90 6 44)" text-anchor="middle">Number of Loads</text>
    <path d="M21,82 C60,80 75,70 90,40 C98,22 102,5 109,5 C116,5 120,22 128,40 C132,48 134,55 137,60 L137,82 Z" fill="#4d4d4d"/>
    <path d="M137,60 C146,74 160,80 198,82 L137,82 Z" fill="#cfcfcf"/>
    <path d="M21,82 C60,80 75,70 90,40 C98,22 102,5 109,5 C116,5 120,22 128,40 C140,66 160,80 198,82" fill="none" stroke="#111" stroke-width=".7"/>
    <polyline points="21,3 198,3 198,83 21,83 21,3" fill="none" stroke="#111" stroke-width=".8"/>
    <line x1="109" y1="3" x2="109" y2="83" stroke="#111" stroke-width=".7"/>
    <line x1="153" y1="3" x2="153" y2="83" stroke="#111" stroke-width=".7"/>
    <polygon points="48,46 62,34 62,40 98,40 98,52 62,52 62,58" fill="#d5d5d5" stroke="#999" stroke-width=".5"/>
    <text x="74" y="50" font-size="7" font-weight="500" fill="#fff">50 %</text>
    <rect x="26" y="10" width="10" height="62" fill="#d5d5d5" stroke="#555" stroke-width=".5"/>
    <text x="34" y="41" font-size="6.5" font-weight="500" transform="rotate(-90 34 41)" text-anchor="middle">Productivity</text>
    <rect x="143" y="8" width="10" height="42" fill="#d5d5d5" stroke="#555" stroke-width=".5"/>
    <text x="151" y="29" font-size="6.5" font-weight="500" transform="rotate(-90 151 29)" text-anchor="middle">Durability</text>
    <rect x="186" y="8" width="12" height="48" fill="#d5d5d5" stroke="#555" stroke-width=".5"/>
    <text x="195" y="32" font-size="6.5" font-weight="500" transform="rotate(-90 195 32)" text-anchor="middle">Tested Limit</text>
    <text x="166" y="72" font-size="8" font-weight="500">10%</text>
    <g font-size="3.4" text-anchor="middle">
      <text x="21" y="89">80</text><text x="43" y="89">85</text><text x="65" y="89">90</text><text x="87" y="89">95</text><text x="109" y="89">100</text><text x="131" y="89">105</text><text x="153" y="89">110</text><text x="175" y="89">115</text><text x="198" y="89">120</text>
      <text x="109" y="97" font-size="4" font-weight="500">% of Target Payload</text>
    </g>
  </svg>
  <div class="footer"><span>© 2024 Brackwyn Mining Solutions Inc.Strictly Confidential</span></div>
  <div class="page"><b>06</b></div>
</section>

<section class="slide col-l row-3">
  <div class="photo" role="img" aria-label="Dark mine waste dumps under an evening sky" style="left:0;top:150px;width:446px;height:90px;background:linear-gradient(180deg,rgba(255,255,255,0) 0%,#b4b7bb 35%,#6a6d72 70%,#4a4d52 100%)"></div>
  <div class="top-band"></div><div class="brand-tab"></div><div class="brand">BRACKWYN</div>
  <div class="title" style="top:26px">WHAT MAKES UP<br>PRODUCTION</div>
  <p class="ln s8" style="left:25px;top:81px">In its simplest terms, we calculate production like this:</p>
  <p class="ln s7 dot strong" style="left:48px;top:103px">This is true for any process</p>
  <p class="ln s6 dot" style="left:72px;top:119px">Mowing the lawn</p>
  <p class="ln s6 dot" style="left:72px;top:132px">Driving</p>
  <p class="ln s6 dot" style="left:72px;top:145px">Mine Production</p>
  <p class="ln s7 dot strong" style="left:48px;top:165px">Production goes up or down because of a change</p>
  <p class="ln s7 strong" style="left:48px;top:177px">in Equipment Productivity or Operating Time</p>
  <svg style="position:absolute;left:0;top:0" width="446" height="250" viewBox="0 0 446 250">
    <g stroke="#c8151f" stroke-width=".8" fill="none">
      <line x1="333" y1="85" x2="333" y2="112"/>
      <line x1="277" y1="112" x2="389" y2="112"/>
      <line x1="277" y1="112" x2="277" y2="129"/>
      <line x1="389" y1="112" x2="389" y2="129"/>
    </g>
    <polygon points="274.5,127 279.5,127 277,131" fill="#c8151f"/>
    <polygon points="386.5,127 391.5,127 389,131" fill="#c8151f"/>
  </svg>
  <div class="pill red" style="left:281px;top:62px;width:104px">PRODUCTION</div>
  <div class="pill dark" style="left:225px;top:131px;width:105px">EQUIPMENT PRODUCTIVITY</div>
  <div class="pill dark" style="left:336px;top:131px;width:105px">OPERATING TIME</div>
  <div class="footer"><span>© 2024 Brackwyn Mining Solutions Inc.Strictly Confidential</span></div>
  <div class="page"><b>03</b></div>
</section>

<section class="slide col-r row-3">
  <div class="top-band"></div><div class="brand-tab"></div><div class="brand">BRACKWYN</div>
  <div class="title" style="top:25px">OVERVIEW – SIC &amp;<br>VISUAL MANAGEMENT</div>
  <p class="ln s65 dot" style="left:41px;top:82px">Dispatchers and Pit Supervisors use the SIC tool to monitor the real-time</p>
  <p class="ln s65" style="left:41px;top:95px">performance of the truck and shovel fleet.</p>
  <p class="ln s65 dot" style="left:41px;top:108px">The tool is monitored hourly to identify underperformance. The dispatcher may</p>
  <p class="ln s65" style="left:41px;top:121px">be the lead in identifying actions for the Pit Supervisor</p>
  <p class="ln s65 dot" style="left:41px;top:134px">Once opportunities or underperforming areas are identified Dispatchers and</p>
  <p class="ln s65" style="left:41px;top:147px">Supervisors will take collaborative action to address them</p>
  <p class="ln s65 dot" style="left:41px;top:160px">The Visual Management process is an accountability check and information</p>
  <p class="ln s65" style="left:41px;top:173px">share. 'Did we monitor the SIC, communicate opportunities and take action</p>
  <svg style="position:absolute;left:274px;top:53px" width="172" height="170" viewBox="0 0 172 170" role="img" aria-label="Digital touchscreen and tablet imagery in diamond frames">
    <defs>
      <linearGradient id="techA" x1="0" y1="0" x2="1" y2="1"><stop offset="0" stop-color="#6fd3e2"/><stop offset="1" stop-color="#12465a"/></linearGradient>
      <linearGradient id="techB" x1="0" y1="0" x2="1" y2="1"><stop offset="0" stop-color="#3a7ea0"/><stop offset="1" stop-color="#0f2a3a"/></linearGradient>
      <linearGradient id="techC" x1="0" y1="0" x2="1" y2="1"><stop offset="0" stop-color="#a5b1b6"/><stop offset="1" stop-color="#4a3a35"/></linearGradient>
    </defs>
    <polygon points="108,0 163,55 108,110 53,55" fill="url(#techA)"/>
    <polygon points="54,57 108,112 54,168 0,112" fill="url(#techB)"/>
    <polygon points="165,58 172,65 172,160 112,112" fill="url(#techC)"/>
  </svg>
  <div class="footer"><span>© 2024 Brackwyn Mining Solutions Inc.Strictly Confidential</span></div>
  <div class="page"><b>07</b></div>
</section>

<section class="slide col-l row-4">
  <div class="top-band"></div><div class="brand-tab"></div><div class="brand">BRACKWYN</div>
  <div class="title" style="top:25px">GENERIC TIME USAGE MODEL</div>
  <p class="ln s75 dot" style="left:41px;top:64px">This is a generic Mining time usage model</p>
  <p class="ln s75 dot" style="left:41px;top:79px">There may be variations from mine-to-mine</p>
  <p class="ln s75" style="left:41px;top:94px">(ie Utilized time vs Operating Time) but this model describes</p>
  <p class="ln s75" style="left:41px;top:109px">everything mine operations needs to know about the</p>
  <p class="ln s75" style="left:41px;top:124px">time usage of a piece of equipment</p>
  <div class="tum">
    <div class="cell c-red" style="left:0;top:0;width:400px;height:16px;border-right:0">Calendar Time</div>
    <div class="cell c-red" style="left:0;top:16px;width:267px;height:15px">Available Time</div>
    <div class="cell c-green" style="left:267px;top:16px;width:133px;height:9px;border-right:0">Down</div>
    <div class="cell c-red" style="left:0;top:31px;width:133px;height:16px">Operating Time</div>
    <div class="cell c-purple" style="left:133px;top:31px;width:67px;height:32px;border-bottom:0">Operating Delay</div>
    <div class="cell c-blue" style="left:200px;top:31px;width:67px;height:32px;border-bottom:0;color:#111">Standby Time</div>
    <div class="cell c-green" style="left:267px;top:25px;width:67px;height:38px;border-bottom:0">Unscheduled</div>
    <div class="cell c-green" style="left:334px;top:25px;width:66px;height:38px;border-bottom:0;border-right:0">Scheduled</div>
    <div class="cell c-red" style="left:0;top:47px;width:66px;height:16px;border-bottom:0">Effective Time</div>
    <div class="cell c-green" style="left:66px;top:47px;width:67px;height:16px;border-bottom:0">Non-Effective Time</div>
  </div>
  <div class="footer"><span>© 2024 Brackwyn Mining Solutions Inc.Strictly Confidential</span></div>
  <div class="page"><b>04</b></div>
</section>

<section class="slide col-r row-4">
  <div class="photo" role="img" aria-label="Yellow mining haul trucks on a dusty haul road" style="left:200px;top:110px;width:246px;height:130px;background:linear-gradient(90deg,#ffffff 0%,rgba(255,255,255,0) 45%),linear-gradient(180deg,#e9eef1 0%,#cfd3d4 35%,#e0b43a 62%,#9a9185 100%)"></div>
  <div class="top-band"></div><div class="brand-tab"></div><div class="brand">BRACKWYN</div>
  <div class="title" style="top:25px">VISUAL MANAGEMENT</div>
  <p class="ln s8" style="left:24px;top:63px">Expectations @ Visual Management Meeting – Dispatchers &amp; Supervisors</p>
  <p class="ln s7 dot strong" style="left:48px;top:86px">For each KPI they are accountable for Dispatcher and Supervisors must report:</p>
  <p class="ln s6 dot" style="left:72px;top:101px">What happened during the shift – Good, bad and changes in KPI</p>
  <p class="ln s6 dot" style="left:72px;top:114px">When were issues identified</p>
  <p class="ln s6 dot" style="left:72px;top:127px">What communication &amp; actions did you take</p>
  <p class="ln s6 dot" style="left:72px;top:141px">Did it improve</p>
  <p class="ln s6 dot" style="left:72px;top:154px">How will KPI look going forward</p>
  <p class="ln s6 dot" style="left:72px;top:167px">Any other actions required</p>
  <p class="ln s7 dot strong" style="left:48px;top:183px">If you are monitoring the SIC during the shift it</p>
  <p class="ln s7 strong" style="left:48px;top:196px">is easy to answer these questions</p>
  <div class="footer"><span>© 2024 Brackwyn Mining Solutions Inc.Strictly Confidential</span></div>
  <div class="page"><b>08</b></div>
</section>

</body>
</html>
```